Brimsett Gardening Fresh New Website

We are looking to create a simple fresh website for our landscaping business. The website should appeal to a 'high end' audience. We deal with a lot of Embassies and affluent clients who have extremely large gardens that are meticulously maintained. The site is about communicating our excellent landscaping and customer service skills and encouraging new clients to reach out and engage us to take care of their gardens.

The website is basically going to be our business card, it will have almost no functionality other than two 'contact us' forms, one for smaller clients and one for more detailed projects.

The website will not have a lot of written content and will have to show photos of beautifully landscaped gardens.

The main logo in black will influence the site, however, we are open to all suggestions.

We are expecting to have the following pages:
Home Page
Services
About Us
Contact Us
Showcase (photo gallery of our work)

We need someone who can code it to wordpress and be available for minor changes over a number of days. They will be simple tweaks.

```html
<!DOCTYPE html>
<html lang="en">
<head>
<meta charset="utf-8">
<title>Brimsett Gardening</title>
<link href="https://fonts.googleapis.com/css2?family=Poppins:ital,wght@0,400;0,500;0,600;0,700;1,600&family=Cinzel:wght@400;600&display=swap" rel="stylesheet">
<style>
:root{
  --gold:#b07a2a;
  --gold-dark:#8a5a14;
  --gold-light:#f1c24a;
  --ink:#1c1812;
  --dark:#211d18;
  --text:#3a3a3a;
  --muted:#8a8a8a;
  --line:#e3e3e3;
  --cream:#fcefdc;
  --white:#ffffff;
}
*{box-sizing:border-box;margin:0;padding:0}
html,body{width:1200px;height:4608px;overflow:hidden;background:var(--white)}
body{font-family:'Poppins',sans-serif;color:var(--text);position:relative}
.btn{position:absolute;display:flex;align-items:center;justify-content:center;background:var(--gold);color:var(--white);font-weight:600;font-size:12px;letter-spacing:.3px;border-radius:4px;text-transform:uppercase}
.section-title{position:absolute;left:0;width:1200px;text-align:center;font-size:36px;font-weight:700;color:var(--ink)}
.section-title span{color:var(--gold-dark)}

/* header */
.site-header{position:absolute;left:0;top:0;width:1200px;height:84px;background:var(--dark)}
.brand{position:absolute;left:141px;top:28px;display:flex;align-items:center;gap:8px;color:var(--gold);font-family:'Poppins',sans-serif;font-weight:500;font-size:11px;line-height:14px}
.brand-dot{width:14px;height:14px;border-radius:50%;background:var(--gold)}
.main-nav{position:absolute;top:32px;left:0;font-size:13px;color:var(--white)}
.main-nav a{position:absolute;white-space:nowrap;color:var(--white);text-decoration:none}
.main-nav a.active{color:var(--gold-light);font-weight:600}

/* hero */
.hero{position:absolute;left:0;top:84px;width:1200px;height:551px;background:linear-gradient(120deg,#6e6a5e 0%,#8a7c62 30%,#4f5c3a 70%,#3d4a2e 100%)}
.hero-tag{position:absolute;left:141px;top:257px;width:272px;height:49px;background:var(--white);color:var(--ink);font-weight:700;font-size:22px;display:flex;align-items:center;justify-content:center}
.hero-title{position:absolute;left:141px;top:318px;width:540px;font-family:'Cinzel',serif;font-weight:400;font-size:35px;line-height:46px;color:var(--white);white-space:nowrap}
.quick{position:absolute;left:710px;top:109px;width:349px;height:504px;background:rgba(255,255,255,.82)}
.tab{position:absolute;top:0;height:32px;display:flex;align-items:center;justify-content:center;font-size:11px;font-weight:600}
.tab.small{left:0;width:170px;background:var(--gold-light);color:var(--ink);clip-path:polygon(0 0,100% 0,88% 100%,0 100%)}
.tab.large{left:150px;width:199px;background:var(--gold-dark);color:var(--white);clip-path:polygon(10% 0,100% 0,100% 100%,0 100%)}
.quick h3{position:absolute;top:48px;width:100%;text-align:center;font-family:'Cinzel',serif;font-weight:400;font-size:19px;color:var(--ink)}
.field{position:absolute;left:16px;width:316px;background:var(--white);border:1px solid var(--line);border-radius:3px;font-size:11px;color:var(--muted);padding:10px 9px}
.checks{position:absolute;left:16px;top:384px;width:316px;font-size:10px;color:var(--text)}
.check{position:absolute;display:flex;align-items:center;gap:6px;white-space:nowrap}
.box{width:12px;height:12px;border:1px solid #999;background:var(--white);border-radius:2px}
.box.on{background:var(--gold-light);border-color:var(--gold)}

/* about */
.about-photo{position:absolute;left:141px;top:728px;width:453px;height:453px;border-radius:50%;background:linear-gradient(180deg,#e9e2d2 0%,#c9c0a8 40%,#7a8c5a 65%,#8f8a7c 100%)}
.about-title{position:absolute;left:667px;top:760px;font-size:22px;font-weight:600;color:var(--ink)}
.about-title span{color:var(--gold-dark)}
.about-text{position:absolute;left:665px;top:808px;width:390px;font-size:12.5px;line-height:21.3px;color:var(--text)}
.about-text p+p{margin-top:21px}

/* services */
.services{position:absolute;left:0;top:1287px;width:1200px;height:663px;background:linear-gradient(180deg,#eef0ec 0%,#f5f6f3 50%,#e6ebe2 100%);border-radius:50% 50% 50% 50% / 40px 40px 40px 40px}
.svc-card{position:absolute;top:1480px;width:218px;height:256px;border-radius:12px;overflow:hidden}
.svc-card .photo{position:absolute;inset:0}
.svc-card .info{position:absolute;left:0;right:0;top:136px;text-align:center;color:var(--white)}
.svc-card h4{font-size:15px;font-weight:600}
.svc-card p{font-size:11px;line-height:16px;margin-top:4px;padding:0 18px}
.svc-card a{display:inline-block;font-size:11px;font-weight:600;color:var(--white);text-decoration:underline;margin-top:6px}

/* gallery */
.tile{position:absolute;width:292px;height:292px;border-radius:14px}

/* testimonials */
.testi-band{position:absolute;left:0;top:2879px;width:1200px;height:617px;background:var(--cream);border-radius:50% 50% 50% 50% / 36px 36px 36px 36px}
.testi{position:absolute;top:3083px;width:292px;height:282px;background:var(--white);border-radius:10px;box-shadow:0 4px 14px rgba(0,0,0,.06);padding:26px 28px}
.stars{color:var(--gold-light);font-size:16px;letter-spacing:4px}
.badge{position:absolute;right:28px;top:26px;width:22px;height:22px;border-radius:50%;border:3px solid #c9c9c9}
.testi p{margin-top:24px;font-size:12.5px;line-height:21px}
.testi h5{margin-top:18px;font-size:15px;font-style:italic;font-weight:700;color:var(--ink)}
.arrow{position:absolute;top:3197px;width:54px;height:54px;border-radius:50%}

/* contact */
.contact-card{position:absolute;left:141px;top:3608px;width:918px;height:429px;background:var(--white);border-radius:18px;box-shadow:0 4px 20px rgba(0,0,0,.08)}
.contact-side{position:absolute;left:141px;top:3608px;width:335px;height:429px;border-radius:18px;background:linear-gradient(160deg,#2a2520 0%,#14110d 100%);color:var(--white)}
.contact-side .kicker{position:absolute;left:36px;top:64px;color:var(--gold);font-size:12px;font-weight:600}
.contact-side h3{position:absolute;left:36px;top:88px;font-size:24px;font-weight:500;line-height:38px}
.c-row{position:absolute;left:36px;display:flex;align-items:center;gap:14px;font-size:12.5px;line-height:21px}
.c-ico{flex:none;width:28px;height:28px;border-radius:50%;border:1.5px solid var(--white);display:flex;align-items:center;justify-content:center}
.form-title{position:absolute;left:515px;top:3643px;font-size:16px;font-weight:600;color:var(--ink)}
.cfield{position:absolute;height:36px;border:1px solid var(--line);border-radius:3px;font-size:11px;color:var(--muted);padding:10px 17px}

/* footer */
.site-footer{position:absolute;left:0;top:4202px;width:1200px;height:406px;background:linear-gradient(180deg,#24201b,#151210);border-radius:50% 50% 0 0 / 40px 40px 0 0}
.foot-badge{position:absolute;left:514px;top:4166px;width:172px;height:172px;border-radius:50%;background:var(--dark);display:flex;align-items:center;justify-content:center;color:var(--gold);font-family:'Poppins',sans-serif;font-weight:500;font-size:15px;line-height:20px;text-align:center}
.foot-nav{position:absolute;left:0;top:4392px;width:1200px;display:flex;justify-content:center;gap:30px;font-size:14px;color:var(--white)}
.foot-line{position:absolute;left:141px;width:918px;height:1px;background:rgba(255,255,255,.35)}
.foot-info{position:absolute;top:4478px;display:flex;gap:12px;align-items:flex-start;color:var(--white);font-size:12px;line-height:20px}
.copy{position:absolute;left:0;top:4561px;width:1200px;text-align:center;color:var(--white);font-size:12px}
</style>
</head>
<body>

<header class="site-header">
  <div class="brand"><span class="brand-dot"></span><span>BRIMSETT<br>GARDENING</span></div>
  <nav class="main-nav">
    <a class="active" style="left:434px">Home</a>
    <a style="left:513px">About Us</a>
    <a style="left:612px">Services</a>
    <a style="left:706px">Gallery</a>
    <a style="left:791px">Contact Us</a>
  </nav>
  <div class="btn" style="left:905px;top:25px;width:154px;height:34px;font-weight:500">Request a Quote</div>
</header>

<section class="hero" role="img" aria-label="Stone house with manicured hedges and lawn"></section>
<div class="hero-tag">BRIMSETT GARDENING</div>
<h1 class="hero-title">YOUR FULL LANDSCAPING<br>&amp; LAWN CARE EXPERTS</h1>
<div class="btn" style="left:141px;top:429px;width:152px;height:34px;font-weight:500">Request a Quote</div>

<form class="quick">
  <div class="tab large">LARGE CLIENTS</div>
  <div class="tab small">SMALLER CLIENTS</div>
  <h3>QUICK CONTACT</h3>
  <div class="field" style="top:82px;height:38px">Name</div>
  <div class="field" style="top:131px;height:37px">Email</div>
  <div class="field" style="top:179px;height:36px">Phone</div>
  <div class="field" style="top:225px;height:38px">Service Type</div>
  <div class="field" style="top:274px;height:100px">Message</div>
  <div class="checks">
    <div class="check" style="left:0;top:0"><span class="box"></span>Weekly Lawn Maintenance</div>
    <div class="check" style="left:212px;top:0"><span class="box"></span>Spring Clean Up</div>
    <div class="check" style="left:0;top:23px"><span class="box on"></span>Fertilizer/weed Control</div>
    <div class="check" style="left:212px;top:23px"><span class="box"></span>Fall Clean Up</div>
    <div class="check" style="left:0;top:46px"><span class="box"></span>Core Aeration</div>
  </div>
  <div class="btn" style="left:16px;top:447px;width:316px;height:39px;font-size:14px;font-weight:500">Submit</div>
</form>

<div class="about-photo" role="img" aria-label="Park bench on a paved promenade with city skyline"></div>
<h2 class="about-title">About <span>Us</span></h2>
<div class="about-text">
  <p>Lorem ipsum dolor sit amet, consectetur adipiscing elit, sed do eiusmod tempor incididunt ut labore et dolore magna aliqua. Quis ipsum suspendisse ultrices gravida. Risus commodo viverra maecenas accumsan lacus vel facilisis. Lorem ipsum dolor sit amet, consectetur adipiscing elit, sed do eiusmod tempor incididunt ut labore et dolore magna aliqua. Quis ipsum suspendisse ultrices gravida. Risus commodo viverra maecenas accumsan lacus vel facilisis.</p>
  <p>Lorem ipsum dolor sit amet, consectetur adipiscing elit, sed do eiusmod tempor incididunt ut labore et dolore magna aliqua. Quis ipsum suspendisse ultrices gravida. Risus commodo viverra maecenas accumsan lacus vel facilisis.</p>
</div>
<div class="btn" style="left:665px;top:1105px;width:112px;height:36px">Read More</div>

<section class="services" role="img" aria-label="Faint park landscape with trees and a pond"></section>
<h2 class="section-title" style="top:1390px">Our <span>Services</span></h2>
<article class="svc-card" style="left:141px">
  <div class="photo" role="img" aria-label="Lone tree on a green lawn" style="background:linear-gradient(180deg,#5f7048,#2f3a26 60%,#1f2419)"></div>
  <div class="info"><h4>Landscaping</h4><p>Lorem ipsum dolor sit amet, consectetur adipiscing.</p><a>Read More</a></div>
</article>
<article class="svc-card" style="left:374px">
  <div class="photo" role="img" aria-label="Gardener trimming a lawn" style="background:linear-gradient(180deg,#8a5a3a,#4a3a2a 60%,#2a2420)"></div>
  <div class="info"><h4>Lawn Service</h4><p>Lorem ipsum dolor sit amet, consectetur adipiscing.</p><a>Read More</a></div>
</article>
<article class="svc-card" style="left:607px">
  <div class="photo" role="img" aria-label="Grass clippings in a mower bag" style="background:linear-gradient(180deg,#6a7858,#3e4634 60%,#26291f)"></div>
  <div class="info"><h4>Lawn Maintenance</h4><p>Lorem ipsum dolor sit amet, consectetur adipiscing.</p><a>Read More</a></div>
</article>
<article class="svc-card" style="left:840px">
  <div class="photo" role="img" aria-label="Arborists working among forest trees" style="background:linear-gradient(180deg,#6e5a44,#3c3428 60%,#24201a)"></div>
  <div class="info"><h4>Tree Services</h4><p>Lorem ipsum dolor sit amet, consectetur adipiscing.</p><a>Read More</a></div>
</article>
<div class="btn" style="left:518px;top:1786px;width:163px;height:38px">View All Services</div>

<h2 class="section-title" style="top:2013px">Our <span>Gallery</span></h2>
<div class="tile" style="left:141px;top:2115px;background:linear-gradient(160deg,#8bb85a,#3e6a2c)" role="img" aria-label="Wooden boardwalk through lush garden"></div>
<div class="tile" style="left:453px;top:2115px;background:linear-gradient(160deg,#9ab860,#4a6a30)" role="img" aria-label="Path beneath green garden arches"></div>
<div class="tile" style="left:764px;top:2115px;background:linear-gradient(180deg,#3a8ad8 0%,#7ab8e8 35%,#c8453a 55%,#5aa040 70%)" role="img" aria-label="Lawn with red flower beds under blue sky"></div>
<div class="tile" style="left:141px;top:2426px;background:linear-gradient(180deg,#c89a5a,#b8a068 50%,#8ab048)" role="img" aria-label="Benches and white fence in an autumn park"></div>
<div class="tile" style="left:453px;top:2426px;background:linear-gradient(160deg,#5a8a3a,#8ab860 50%,#a89878)" role="img" aria-label="Stone steps beside a waterfall garden"></div>
<div class="tile" style="left:764px;top:2426px;background:linear-gradient(180deg,#9aa890,#6a8a50 55%,#3a6a28)" role="img" aria-label="Stone gazebo surrounded by clipped shrubs"></div>
<div class="btn" style="left:524px;top:2766px;width:150px;height:39px">View All Gallery</div>

<section class="testi-band"></section>
<h2 class="section-title" style="top:2984px">Client <span>Testimonials</span></h2>
<div class="arrow" style="left:64px;border:2px solid var(--gold)">
  <svg width="50" height="50" viewBox="0 0 50 50"><path d="M29 15 L19 25 L29 35" fill="none" stroke="#b07a2a" stroke-width="3" stroke-linecap="round"/></svg>
</div>
<div class="arrow" style="left:1080px;background:var(--gold)">
  <svg width="54" height="54" viewBox="0 0 54 54"><path d="M23 17 L33 27 L23 37" fill="none" stroke="#fff" stroke-width="3" stroke-linecap="round"/></svg>
</div>
<article class="testi" style="left:141px"><div class="stars">★★★★★</div><span class="badge"></span><p>Lorem ipsum dolor sit amet, consectetur adipiscing elit, sed do eiusmod tempor incididunt ut labore et dolore magna aliqua. Quis ipsum suspendisse ultrices gravida. Risus commodo viverra maecenas accumsan lacus vel facilisis.</p><h5>Marta Ellison</h5></article>
<article class="testi" style="left:453px"><div class="stars">★★★★★</div><span class="badge"></span><p>Lorem ipsum dolor sit amet, consectetur adipiscing elit, sed do eiusmod tempor incididunt ut labore et dolore magna aliqua. Quis ipsum suspendisse ultrices gravida. Risus commodo viverra maecenas accumsan lacus vel facilisis.</p><h5>Marta Ellison</h5></article>
<article class="testi" style="left:764px"><div class="stars">★★★★★</div><span class="badge"></span><p>Lorem ipsum dolor sit amet, consectetur adipiscing elit, sed do eiusmod tempor incididunt ut labore et dolore magna aliqua. Quis ipsum suspendisse ultrices gravida. Risus commodo viverra maecenas accumsan lacus vel facilisis.</p><h5>Marta Ellison</h5></article>

<div class="contact-card"></div>
<aside class="contact-side">
  <div class="kicker">CONTACT US</div>
  <h3>Ask One Of Our<br>Experts For Help</h3>
  <div class="c-row" style="top:183px"><span class="c-ico"><svg width="14" height="14" viewBox="0 0 24 24"><path d="M6 3h4l2 5-3 2a11 11 0 0 0 5 5l2-3 5 2v4a2 2 0 0 1-2 2A17 17 0 0 1 4 5a2 2 0 0 1 2-2z" fill="none" stroke="#fff" stroke-width="2"/></svg></span>+91 123-456-7890</div>
  <div class="c-row" style="top:237px"><span class="c-ico"><svg width="14" height="14" viewBox="0 0 24 24"><rect x="3" y="6" width="18" height="12" fill="none" stroke="#fff" stroke-width="2"/><path d="M3 6l9 7 9-7" fill="none" stroke="#fff" stroke-width="2"/></svg></span>hello@brimsettgardening.com</div>
  <div class="c-row" style="top:288px"><span class="c-ico"><svg width="14" height="14" viewBox="0 0 24 24"><path d="M12 22s7-7 7-12a7 7 0 0 0-14 0c0 5 7 12 7 12z" fill="none" stroke="#fff" stroke-width="2"/><circle cx="12" cy="10" r="2.5" fill="#fff"/></svg></span>Lorem Ipsum is simply of the<br>printing and typesetting industry.</div>
</aside>
<h3 class="form-title">DROP YOUR MESSAGE</h3>
<div class="cfield" style="left:515px;top:3696px;width:247px;border-color:var(--gold);color:var(--ink)">First Name</div>
<div class="cfield" style="left:771px;top:3696px;width:248px">Last Name</div>
<div class="cfield" style="left:515px;top:3744px;width:247px">Email Address</div>
<div class="cfield" style="left:771px;top:3744px;width:248px">Phone</div>
<div class="cfield" style="left:515px;top:3796px;width:504px;height:136px">Message</div>
<div class="btn" style="left:515px;top:3959px;width:127px;height:39px">Submit Now</div>

<footer class="site-footer"></footer>
<div class="foot-badge"><span>BRIMSETT<br>GARDENING</span></div>
<nav class="foot-nav"><span>Home</span><span>About Us</span><span>Services</span><span>Our Gallery</span><span>Contact Us</span></nav>
<div class="foot-line" style="top:4451px"></div>
<div class="foot-info" style="left:141px"><svg width="22" height="22" viewBox="0 0 24 24"><circle cx="12" cy="12" r="9" fill="none" stroke="#fff" stroke-width="1.5"/><path d="M3 12h18M12 3a14 14 0 0 1 0 18M12 3a14 14 0 0 0 0 18" fill="none" stroke="#fff" stroke-width="1.5"/></svg><span>Lorem Ipsum is simply dummy text<br>of the printing and typesetting.</span></div>
<div class="foot-info" style="left:508px"><svg width="22" height="22" viewBox="0 0 24 24"><path d="M6 3h4l2 5-3 2a11 11 0 0 0 5 5l2-3 5 2v4a2 2 0 0 1-2 2A17 17 0 0 1 4 5a2 2 0 0 1 2-2z" fill="none" stroke="#fff" stroke-width="1.5"/></svg><span>Call Us<br>123-456-7890</span></div>
<div class="foot-info" style="left:798px"><svg width="22" height="22" viewBox="0 0 24 24"><rect x="3" y="6" width="18" height="12" fill="none" stroke="#fff" stroke-width="1.5"/><path d="M3 6l9 7 9-7" fill="none" stroke="#fff" stroke-width="1.5"/></svg><span>Email<br>hello@brimsettgardening.com</span></div>
<div class="foot-line" style="top:4536px"></div>
<div class="copy">© 2024 Brimsett Landscaping Gardening. All Rights Reserved.</div>

</body>
</html>
```